Visitenkarte für Ergotherapiepraxis
Zielgruppe
Wir arbeiten mit Kindern und Erwachsene jeden Alters.
Diese Personen kommen mit Beeinträchtigungen (körperlich, seelisch, schulisch) im täglichen Leben zu uns. Wir unterstützen unsere Patienten die Beeinträchtigungen zu verringern oder zu kompensieren und so den Alltag besser bewältigen zu können.
Aufgabenstellung
Ein Design was Kinder und Erwachsene anspricht, aber nicht zu verspielt wirkt. Es soll vertrauenserweckend sein. Eventuell sollte die Visitenkarte ein "aufgehendes oder erblühendes oder aufsteigendes" Element enthalten (=zu Beginn war die Beeinträchtigung dann steigt die Lebensqualität als Folge der Behandlung)
Daten vorn:
Ergotherapiepraxis

```html
<!DOCTYPE html>
<html lang="de">
<head>
<meta charset="utf-8">
<title>Visitenkarte Ergotherapiepraxis</title>
<link href="https://fonts.googleapis.com/css2?family=Roboto:ital,wght@0,400;1,400&display=swap" rel="stylesheet">
<style>
  :root {
    --green-dark: #1f8a2b;
    --green-light: #7cc242;
    --green-pale: #b9df93;
    --ink: #1a1a1a;
    --card-border: #d9d9d9;
    --page: #ffffff;
  }
  html, body {
    margin: 0;
    padding: 0;
    width: 1057px;
    height: 1200px;
    overflow: hidden;
    background: var(--page);
    font-family: "Roboto", Arial, sans-serif;
  }
  .canvas {
    position: relative;
    width: 1057px;
    height: 1200px;
  }
  .card {
    position: absolute;
    left: 12px;
    width: 1030px;
    height: 562px;
    box-sizing: border-box;
    border: 2px solid var(--card-border);
    border-radius: 6px;
    background: #fff;
    box-shadow: 0 1px 3px rgba(0,0,0,0.08);
  }
  .card--front { top: 20px; }
  .card--back { top: 628px; }

  .illustration-area {
    position: absolute;
    left: 61px;
    top: 53px;
    width: 345px;
    height: 474px;
    border-radius: 8px;
    background: linear-gradient(180deg, var(--green-pale) 0%, var(--green-light) 55%, var(--green-dark) 100%);
  }

  .front-details {
    position: absolute;
    right: 60px;
    top: 122px;
    text-align: right;
  }
  .therapist-name {
    margin: 0;
    font-size: 62px;
    font-weight: 400;
    line-height: 1.1;
    color: var(--green-dark);
    letter-spacing: -0.5px;
  }
  .practice-type {
    margin: 10px 0 0;
    font-size: 38px;
    line-height: 1.2;
    color: var(--green-light);
  }
  .address {
    margin: 64px 0 0;
    font-style: italic;
    font-size: 36px;
    line-height: 47px;
    color: var(--ink);
  }

  .back-label {
    position: absolute;
    left: 420px;
    right: 40px;
    top: 192px;
    margin: 0;
    text-align: center;
    font-size: 80px;
    font-weight: 400;
    line-height: 86px;
    color: var(--green-dark);
  }
</style>
</head>
<body>
<div class="canvas">

  <section class="card card--front">
    <div class="illustration-area" role="img" aria-label="Illustration: grüner Baum aus Blättern, dessen Stamm eine Familie bildet"></div>
    <div class="front-details">
      <h1 class="therapist-name">Marlene Seidel</h1>
      <p class="practice-type">Ergotherapiepraxis</p>
      <p class="address">Am Lindenhang 12<br>14712 Wiesenfeld, OT Birkau<br>Tel. 033845/47190</p>
    </div>
  </section>

  <section class="card card--back">
    <div class="illustration-area" role="img" aria-label="Illustration: grüner Baum aus Blättern, dessen Stamm eine Familie bildet"></div>
    <h2 class="back-label">Behandelnder<br>Therapeut</h2>
  </section>

</div>
</body>
</html>
```